Electrician Letterhead Design MVR

We need some letterhead for our bills and other papers.
Customer address is on the right side (Swiss format)
A4 format

Design should also be applicable on Cards

Target Market(s)

Private Customers, Small Business

Industry/Entity Type

Electrician

Other font styles liked:
• incised 901

Colors
00AB8E
00BBA5
67D7C9
C6EFE9
E9F9F6

```html
<!DOCTYPE html>
<html lang="de">
<head>
<meta charset="utf-8">
<title>MVR Letterhead</title>
<link rel="stylesheet" href="https://fonts.googleapis.com/css2?family=PT+Serif:wght@400;700&display=swap">
<style>
  :root {
    --backdrop: #dbdbdb;
    --paper: #ffffff;
    --brand: #0a9e8a;
    --ink: #1c1c1c;
    --rule: #6b6b6b;
    --ghost: #ececec;
  }
  * { margin: 0; padding: 0; box-sizing: border-box; }
  html, body { width: 1200px; height: 947px; overflow: hidden; }
  body {
    background: var(--backdrop);
    font-family: "PT Serif", serif;
    position: relative;
  }
  .letterhead {
    position: absolute;
    left: 364px; top: 179px;
    width: 472px; height: 605px;
    background: var(--paper);
    overflow: hidden;
  }
  .brand {
    position: absolute;
    left: 0; right: 0; top: 14px;
    text-align: center;
    color: var(--brand);
  }
  .brand-name {
    display: block;
    font-weight: 700;
    font-size: 44px;
    line-height: 44px;
    letter-spacing: 1px;
  }
  .brand-tagline {
    display: block;
    font-size: 6.5px;
    color: var(--ink);
    margin-top: 1px;
  }
  .backdrop-mark {
    position: absolute;
    left: 0; right: 0; top: 200px;
    text-align: center;
    font-weight: 700;
    font-size: 170px;
    line-height: 170px;
    color: var(--ghost);
    user-select: none;
  }
  .contact-rule {
    position: absolute;
    left: 34px; width: 409px; top: 560px;
    border-top: 1px solid var(--rule);
  }
  .contact-bar {
    position: absolute;
    left: 36px; right: 33px; top: 572px;
    display: flex;
    justify-content: space-between;
    align-items: center;
  }
  .contact-item { display: flex; align-items: center; gap: 5px; }
  .contact-icon {
    width: 20px; height: 20px;
    background: var(--brand);
    display: flex; align-items: center; justify-content: center;
    flex: none;
  }
  .contact-text {
    font-size: 10px;
    line-height: 12.5px;
    color: var(--ink);
  }
  .contact-text.align-right { text-align: right; }
</style>
</head>
<body>
  <main class="letterhead">
    <header class="brand">
      <span class="brand-name">MVR</span>
      <span class="brand-tagline">Meister Volt Regio GmbH</span>
    </header>

    <div class="backdrop-mark" aria-hidden="true">MVR</div>

    <div class="contact-rule"></div>
    <footer class="contact-bar">
      <div class="contact-item">
        <span class="contact-icon">
          <svg width="12" height="12" viewBox="0 0 24 24" fill="none" stroke="#fff" stroke-width="2" stroke-linecap="round" stroke-linejoin="round"><path d="M22 16.9v3a2 2 0 0 1-2.2 2 19.8 19.8 0 0 1-8.6-3.1 19.5 19.5 0 0 1-6-6A19.8 19.8 0 0 1 2.1 4.2 2 2 0 0 1 4.1 2h3a2 2 0 0 1 2 1.7c.1.9.4 1.8.7 2.7a2 2 0 0 1-.5 2.1L8 9.8a16 16 0 0 0 6 6l1.3-1.3a2 2 0 0 1 2.1-.4c.9.3 1.8.6 2.7.7a2 2 0 0 1 1.7 2z"/></svg>
        </span>
        <div class="contact-text">044-123 456 789<br>044-123 456 789</div>
      </div>
      <div class="contact-item">
        <span class="contact-icon">
          <svg width="12" height="12" viewBox="0 0 24 24" fill="none" stroke="#fff" stroke-width="1.8"><circle cx="12" cy="12" r="10"/><ellipse cx="12" cy="12" rx="4.5" ry="10"/><path d="M2 12h20M4 7h16M4 17h16"/></svg>
        </span>
        <div class="contact-text">info@webname.com<br>www.websitename.com</div>
      </div>
      <div class="contact-item">
        <span class="contact-icon">
          <svg width="11" height="12" viewBox="0 0 24 24"><path fill="#fff" d="M12 1a8 8 0 0 0-8 8c0 6 8 14 8 14s8-8 8-14a8 8 0 0 0-8-8zm0 11a3 3 0 1 1 0-6 3 3 0 0 1 0 6z"/></svg>
        </span>
        <div class="contact-text align-right">Your Address line here<br>Country Code 0123456</div>
      </div>
    </footer>
  </main>
</body>
</html>
```